Business Card for Fashion House

We need a business card design for our personalize fashion service for our customers. the business card should reflect reliability, luxury and creativity.
The brand Gravetto is extracted from "Graceful Velvetto"; Gravetto provides fashion designs sprinkled with luxury and style tailored for our elite clients character profile.
Gravetto is created for those who embody class and elegance with a passion for style.
Target Market(s)
Affluent Customers
Industry/Entity Type
Fashion
Contact Information for Business Card
Samira Haddadin
Fashion Designer
Telephone: +971 4 555 0192
Mobile +971 50 555 0147
Emal info@gravetto-example.com
Website www.gravetto-example.com
Social Media Youtube g+ Facebook Instagram Pin /gravetto
Font styles to use
Other font styles liked:
- Audrey provided
Look and feel
Each slider illustrates characteristics of the customer's brand and the style your logo design should communicate.

```html
<!DOCTYPE html>
<html lang="en">
<head>
<meta charset="utf-8">
<title>Gravetto Business Card</title>
<link rel="stylesheet" href="https://fonts.googleapis.com/css2?family=Marcellus&family=Cinzel:wght@400;600&family=Open+Sans:wght@400;600&display=swap">
<style>
  :root {
    --canvas: #e9e7e4;
    --card-dark: #3b3331;
    --card-light: #f4f4f4;
    --ink: #1c1c1c;
    --ink-soft: #3a3a3a;
    --white: #ffffff;
    --muted: #8d8886;
    --band-dark: #2f2f2f;
    --band-grey: #cfcfcf;
    --band-grey-deep: #b5b5b5;
  }
  * { margin: 0; padding: 0; box-sizing: border-box; }
  html, body { width: 1200px; height: 1000px; overflow: hidden; }
  body { background: var(--canvas); position: relative; font-family: "Marcellus", serif; }

  .card {
    position: absolute;
    left: 215px;
    width: 770px;
    height: 440px;
    border-radius: 22px;
    overflow: hidden;
    box-shadow: 0 10px 28px rgba(0,0,0,0.18);
  }

  /* Back of card */
  .card-back { top: 40px; background: var(--card-dark); color: var(--white); }
  .card-back .brand-mark {
    position: absolute; left: 0; right: 0; top: 120px;
    display: flex; flex-direction: column; align-items: center; gap: 34px;
  }
  .card-back .brand-dot {
    width: 74px; height: 74px; border-radius: 50%;
    border: 5px solid var(--white);
  }
  .card-back .brand-name {
    font-size: 50px; letter-spacing: 22px; margin-right: -22px;
    color: var(--white);
  }
  .card-back .brand-web {
    position: absolute; left: 0; right: 0; bottom: 58px; text-align: center;
    font-family: "Open Sans", sans-serif; font-size: 19px; color: var(--muted);
    letter-spacing: 0.5px;
  }

  /* Front of card */
  .card-front { top: 520px; background: var(--card-light); color: var(--ink); }
  .card-front .band { position: absolute; inset: 0; }

  .card-front .brand-mark {
    position: absolute; left: 110px; top: 48px;
    display: flex; flex-direction: column; align-items: flex-start; gap: 26px;
  }
  .card-front .brand-dot {
    width: 58px; height: 58px; border-radius: 50%;
    border: 4px solid var(--ink); margin-left: 40px;
  }
  .card-front .brand-name {
    font-size: 30px; letter-spacing: 13px; color: var(--ink);
  }

  .contact-list {
    position: absolute; left: 110px; top: 250px;
    list-style: none; font-size: 15.5px; color: var(--ink);
  }
  .contact-list li { display: flex; align-items: center; gap: 12px; height: 25px; }
  .contact-list svg { width: 15px; height: 15px; flex: none; }

  .person {
    position: absolute; left: 480px; top: 150px;
  }
  .person-name { font-size: 25px; letter-spacing: 0.5px; color: var(--ink); }
  .person-role { font-size: 15px; color: var(--ink-soft); margin-top: 2px; }

  .social-row {
    position: absolute; left: 530px; top: 306px;
    display: flex; align-items: center; gap: 9px;
    color: var(--white); font-size: 15px;
  }
  .social-dot {
    width: 17px; height: 17px; border-radius: 50%;
    background: var(--white);
  }
  .social-handle { margin-left: 4px; letter-spacing: 0.5px; }
</style>
</head>
<body>

  <section class="card card-back" aria-label="Business card back">
    <div class="brand-mark">
      <span class="brand-dot"></span>
      <span class="brand-name">GRAVETTO</span>
    </div>
    <p class="brand-web">www.gravetto-example.com</p>
  </section>

  <section class="card card-front" aria-label="Business card front">
    <svg class="band" viewBox="0 0 770 440" preserveAspectRatio="none" aria-hidden="true">
      <path d="M0 408 H 420 C 440 408 448 398 452 384 L 466 322 C 470 306 478 296 494 296 H 770 V 440 H 0 Z" fill="var(--band-grey-deep)"/>
      <path d="M0 418 H 430 C 452 418 460 406 464 392 L 476 340 C 480 328 488 322 500 322 H 770 V 440 H 0 Z" fill="var(--band-grey)"/>
      <path d="M494 296 H 770 V 338 H 506 C 498 338 494 332 492 326 L 488 310 C 486 302 488 296 494 296 Z" fill="var(--band-dark)"/>
    </svg>

    <div class="brand-mark">
      <span class="brand-dot"></span>
      <span class="brand-name">GRAVETTO</span>
    </div>

    <ul class="contact-list">
      <li>
        <svg viewBox="0 0 16 16" aria-hidden="true"><rect x="4" y="1" width="8" height="14" rx="1.5" fill="none" stroke="currentColor" stroke-width="1.4"/><circle cx="8" cy="12.5" r="0.9" fill="currentColor"/></svg>
        +971 4 555 0192
      </li>
      <li>
        <svg viewBox="0 0 16 16" aria-hidden="true"><path d="M3 2 L6 2 L7 5.5 L5.3 6.8 C6.2 8.8 7.4 10 9.2 10.8 L10.5 9 L14 10 L14 13 C14 13.6 13.5 14 13 14 C7.4 13.7 2.4 8.7 2 3 C2 2.4 2.4 2 3 2 Z" fill="currentColor"/></svg>
        +971 50 555 0147
      </li>
      <li>
        <svg viewBox="0 0 16 16" aria-hidden="true"><circle cx="8" cy="8" r="6.5" fill="none" stroke="currentColor" stroke-width="1.3"/><ellipse cx="8" cy="8" rx="2.8" ry="6.5" fill="none" stroke="currentColor" stroke-width="1.1"/><line x1="1.5" y1="8" x2="14.5" y2="8" stroke="currentColor" stroke-width="1.1"/></svg>
        www.gravetto-example.com
      </li>
      <li>
        <svg viewBox="0 0 16 16" aria-hidden="true"><rect x="1.5" y="3.5" width="13" height="9" rx="1" fill="none" stroke="currentColor" stroke-width="1.3"/><path d="M1.8 4 L8 9 L14.2 4" fill="none" stroke="currentColor" stroke-width="1.3"/></svg>
        info@gravetto-example.com
      </li>
    </ul>

    <div class="person">
      <p class="person-name">SAMIRA HADDADIN</p>
      <p class="person-role">Fashion Designer</p>
    </div>

    <div class="social-row" aria-label="Social media: /gravetto">
      <span class="social-dot"></span>
      <span class="social-dot"></span>
      <span class="social-dot"></span>
      <span class="social-dot"></span>
      <span class="social-dot"></span>
      <span class="social-handle">/gravetto</span>
    </div>
  </section>

</body>
</html>
```